Im open to ideas.. I was thinking on my business cards aswell as my logo. a place for my name. email. phone number and abn..

ive attched a file with my business logo. which i dont love the colours.. i was think a dark background with charcoal letters so something along those colour schumes but im open to ideas..

BRM Constructions

```html
<!DOCTYPE html>
<html lang="en">
<head>
<meta charset="utf-8">
<title>BRM Constructions – Business Cards</title>
<link rel="stylesheet" href="https://fonts.googleapis.com/css2?family=Arimo:wght@400;700&display=swap">
<style>
  :root {
    --backdrop: #2f2825;
    --card: #161616;
    --card-edge: #222222;
    --ink-white: #ffffff;
    --ink-soft: #d9d9d9;
    --ink-muted: #8c8c8c;
    --gloss: #4a4a4a;
    --accent: #e3262b;
  }
  * { box-sizing: border-box; margin: 0; padding: 0; }
  html, body { width: 1200px; height: 787px; overflow: hidden; }
  body {
    background: var(--backdrop);
    font-family: "Arimo", Arial, sans-serif;
    position: relative;
  }
  .card {
    position: absolute;
    top: 243px;
    width: 530px;
    height: 300px;
    background: var(--card);
    border: 1px solid var(--card-edge);
    border-radius: 4px;
    box-shadow: 0 14px 30px rgba(0,0,0,0.45);
  }
  .card--back { left: 45px; }
  .card--front { left: 625px; }

  .brand {
    display: flex;
    align-items: center;
    gap: 14px;
    font-weight: 700;
    letter-spacing: 2px;
    text-transform: uppercase;
  }
  .brand__mark { width: 22px; height: 22px; flex: none; }
  .brand__name { font-size: 34px; line-height: 1; }

  .card--back .brand { position: absolute; left: 60px; top: 100px; }
  .card--back .brand__mark { background: var(--gloss); }
  .card--back .brand__name { color: var(--gloss); }
  .card--back .website {
    position: absolute; left: 60px; top: 200px;
    color: var(--ink-soft);
    font-size: 14px;
    letter-spacing: 4px;
  }

  .card--front .brand { position: absolute; left: 150px; top: 80px; }
  .card--front .brand__mark { background: var(--accent); }
  .card--front .brand__name { color: var(--ink-white); }

  .person {
    position: absolute; left: 60px; top: 190px;
    text-align: right; width: 140px;
  }
  .person__name { color: var(--accent); font-size: 18px; }
  .person__role { color: var(--ink-white); font-size: 16px; margin-top: 4px; }

  .divider {
    position: absolute; left: 222px; top: 182px;
    width: 1px; height: 86px;
    background: var(--ink-muted);
  }

  .contact {
    position: absolute; left: 244px; top: 186px;
    list-style: none;
    color: var(--ink-soft);
    font-size: 15px;
  }
  .contact li { display: flex; align-items: center; gap: 10px; height: 26px; }
  .contact__icon { width: 14px; height: 14px; fill: var(--accent); flex: none; }
  .contact__spacer { width: 14px; flex: none; }
</style>
</head>
<body>
  <section class="card card--back" aria-label="Business card back">
    <div class="brand">
      <span class="brand__mark"></span>
      <span class="brand__name">BRM Constructions</span>
    </div>
    <p class="website">www.brmbuild.com</p>
  </section>

  <section class="card card--front" aria-label="Business card front">
    <div class="brand">
      <span class="brand__mark"></span>
      <span class="brand__name">BRM Constructions</span>
    </div>

    <div class="person">
      <p class="person__name">Sam Carter</p>
      <p class="person__role">President</p>
    </div>

    <span class="divider"></span>

    <ul class="contact">
      <li><span class="contact__spacer"></span>ABN: 123456789</li>
      <li>
        <svg class="contact__icon" viewBox="0 0 16 16" aria-hidden="true">
          <path d="M2 5c0-2 2-3 6-3s6 1 6 3v1h-3V4.5C10 4 9 4 8 4s-2 0-3 .5V6H2z"/>
          <rect x="3" y="8" width="10" height="6" rx="1"/>
        </svg>
        555 0142 7781
      </li>
      <li>
        <svg class="contact__icon" viewBox="0 0 16 16" aria-hidden="true">
          <path d="M1 3h14v10H1z M2 4l6 5 6-5" fill="var(--accent)" stroke="var(--card)" stroke-width="1"/>
        </svg>
        sam@brmbuild.com
      </li>
    </ul>
  </section>
</body>
</html>
```